Online Shop - Website Design for up an coming art studio

We require a fully functional website design - not just design - but complete coded online shop website please, which should be a word press style frame work to allow ease up updating the site in the future. The website will sell art work from up and coming artists. The business is called "Brindle Harbor Studios". I have attached our logo to allow the submitted designs to tie in with this.

Industry/Entity Type

Shop

Coding

Coded - Design and coding required

Number of Pages Required

1 page

Colors

Designer to choose colors to be used in the design.

Requirements
Must have
• The website design must incorporate and fully functional online eCommerce shop feature.

```html
<!DOCTYPE html>
<html lang="en">
<head>
<meta charset="utf-8">
<title>Brindle Harbor Studios</title>
<link rel="stylesheet" href="https://fonts.googleapis.com/css2?family=Open+Sans:wght@400;600;700&family=Oswald:wght@500;700&display=swap">
<style>
:root{
  --ink:#222;
  --text:#555;
  --muted:#888;
  --red:#e0323f;
  --pink:#e5177e;
  --dark:#333;
  --frame:#3b3b3b;
  --bg:#f6f6f6;
  --white:#fff;
  --star:#f2b01e;
  --orange:#f39a1e;
  --blue:#2aa3dc;
  --green:#8cc63f;
}
*{box-sizing:border-box;margin:0;padding:0}
html,body{width:1200px;height:3482px;overflow:hidden}
body{background:var(--bg);font-family:"Open Sans",Arial,sans-serif;color:var(--text);position:relative}
.abs{position:absolute}

/* header */
.brand{left:97px;top:30px;width:190px;text-align:center}
.brand-mark{width:72px;height:72px;border-radius:50%;background:var(--dark);margin:0 auto 8px}
.brand-name{font-size:20px;font-weight:700;color:var(--dark);letter-spacing:.5px;line-height:1.1}
.address{left:560px;top:80px;width:250px;text-align:right;font-size:12px;line-height:17px;color:var(--ink)}
.pin{left:816px;top:78px;width:36px;height:36px;border-radius:50%;border:2px solid var(--red);display:flex;align-items:center;justify-content:center}
.account{right:100px;top:42px;font-size:13px;color:var(--ink)}
.search{left:877px;top:82px;width:223px;height:32px;border:1px solid #ccc;border-radius:16px;background:var(--white);font-size:11px;color:var(--muted);padding:8px 16px;display:flex;justify-content:space-between;align-items:center}

.nav{left:97px;top:167px;width:1003px;height:53px;background:var(--dark);display:flex;align-items:center}
.nav a{color:var(--white);font-size:13px;font-weight:600;text-decoration:none;padding:0 30px 0 32px;letter-spacing:.3px}
.cart{position:absolute;right:0;top:0;width:125px;height:53px;background:var(--red);color:var(--white);display:flex;align-items:center;justify-content:center;gap:10px;font-size:14px;font-weight:600}

/* hero */
.hero{left:97px;top:225px;width:1003px;height:483px;border:4px solid #555;background:linear-gradient(135deg,#8f97d9 0%,#c7c2ee 30%,#5b6fc4 55%,#b9b4e8 75%,#7e8ad0 100%)}
.hero-badge{left:480px;top:375px;width:182px;height:182px;border-radius:50%;background:var(--white);border:9px solid #e8737b;display:flex;flex-direction:column;align-items:center;justify-content:center;font-family:"Oswald",sans-serif;color:var(--dark);line-height:1}
.hero-badge .l1{font-size:36px;font-weight:700}
.hero-badge .l2{font-size:32px;font-weight:700;margin-top:2px}
.hero-badge .l3{display:flex;align-items:center;margin-top:4px}
.hero-badge .num{font-size:36px;font-weight:700}
.hero-badge .pct{display:flex;flex-direction:column;align-items:center;margin-left:2px}
.hero-badge .pct small{font-size:12px;font-weight:500;line-height:1}
.hero-badge .pct b{font-size:22px;font-weight:700;line-height:1}
.arrow{width:34px;height:34px;background:rgba(40,40,40,.8);display:flex;align-items:center;justify-content:center}

/* welcome */
.welcome-title{left:0;top:750px;width:1200px;text-align:center;font-size:31px;font-weight:700;color:var(--ink);letter-spacing:.5px}
.welcome-title span{color:var(--red)}
.welcome-text{left:160px;top:800px;width:880px;text-align:center;font-size:11.5px;line-height:21px}

/* frames */
.frame{background:var(--frame);box-shadow:0 8px 14px rgba(0,0,0,.35);padding:12px}
.mat{background:var(--white);padding:18px;height:100%}
.art{width:100%;height:100%}
.big-frame{height:313px;width:316px;padding:12px 12px 52px}
.big-frame .label{position:absolute;left:0;bottom:16px;width:100%;text-align:center;color:var(--white);font-size:12.5px;font-weight:600}

/* banner */
.banner{left:97px;top:1277px;width:1003px;height:436px;background:linear-gradient(90deg,#c2301f 0%,#d24a36 22%,#8c8c8c 40%,#bdbdbd 62%,#d8d8d8 100%)}
.sale{left:476px;top:1333px;width:124px;height:124px;border-radius:50%;background:#d4392b;border:4px solid rgba(255,255,255,.6);color:var(--white);display:flex;flex-direction:column;align-items:center;justify-content:center;font-weight:700}
.sale .s1{font-size:15px}
.sale .s2{font-size:26px}
.banner-title{left:668px;top:1313px;font-size:32px;font-weight:700;color:var(--dark);line-height:38px;letter-spacing:.5px}
.banner-text{left:668px;top:1392px;width:370px;font-size:11.5px;line-height:19px;color:var(--ink)}
.btn-shop{left:668px;top:1465px;width:112px;height:27px;background:var(--red);color:var(--white);font-size:11px;font-weight:700;display:flex;align-items:center;justify-content:center}

/* tabs */
.tabs{left:297px;top:1773px;height:42px;display:flex;gap:4px}
.tab{height:42px;display:flex;align-items:center;justify-content:center;color:var(--white);font-size:14.5px;font-weight:600;background:var(--dark)}
.tab.active{background:var(--pink);width:193px;clip-path:polygon(6% 0,100% 0,100% 100%,0 100%)}
.tab.t2{width:220px}
.tab.t3{width:158px;clip-path:polygon(0 0,92% 0,100% 100%,0 100%)}

.product-frame{width:223px;height:236px;padding:10px}
.product-frame .mat{padding:16px}
.p-name{font-size:16px;color:var(--ink)}
.p-price{font-size:13px;color:var(--red);font-weight:600}
.p-price .stars{color:var(--star);letter-spacing:1px;margin-left:6px}
.p-price .off{color:#ccc}

/* features */
.features{left:0;top:2228px;width:1200px;height:344px;background:linear-gradient(90deg,#3a2233 0%,#6a3a22 30%,#2e2c4c 55%,#5b1d3a 80%,#2a2c38 100%)}
.feature{width:350px;text-align:center;color:var(--white)}
.f-icon{width:92px;height:92px;border-radius:50%;margin:0 auto 28px;display:flex;align-items:center;justify-content:center}
.f-title{font-size:14px;font-weight:700;margin-bottom:12px;letter-spacing:.3px}
.f-text{font-size:12.5px;line-height:20px;color:#eee}

/* blogs */
.blogs-title{left:0;top:2638px;width:1200px;text-align:center;font-size:31px;font-weight:600;color:var(--ink)}
.blog{width:316px;height:308px;background:var(--white);box-shadow:0 1px 3px rgba(0,0,0,.12)}
.blog .img{height:174px}
.blog .body{padding:14px 16px}
.b-title{font-size:15px;color:var(--ink);margin-bottom:10px}
.b-meta{font-size:12.5px;color:var(--ink);margin-bottom:12px;display:flex;align-items:center;gap:6px}
.b-text{font-size:12px;line-height:20px;color:var(--text)}

/* footer */
.footer{left:0;top:3115px;width:1200px;height:315px;background:linear-gradient(120deg,#f4ecef 0%,#eef0f6 40%,#f3f1ea 70%,#eeeeee 100%)}
.f-head{font-size:17px;font-weight:700;color:var(--ink);letter-spacing:.5px}
.news-text{left:97px;top:3220px;width:250px;font-size:11.5px;line-height:19px}
.news-input{left:97px;top:3268px;width:245px;height:40px;background:var(--white);border:1px solid #ddd;font-size:11px;padding:12px;color:var(--ink)}
.news-btn{left:97px;top:3320px;width:122px;height:40px;background:var(--red);color:var(--white);font-size:12px;font-weight:700;display:flex;align-items:center;justify-content:center}
.contact-row{display:flex;gap:14px;font-size:12.5px;line-height:20px;color:var(--ink);margin-bottom:14px;align-items:flex-start}
.links li{list-style:none;font-size:11.5px;color:var(--ink);line-height:23px;display:flex;align-items:center;gap:10px}
.links li::before{content:"";border-left:5px solid var(--ink);border-top:4px solid transparent;border-bottom:4px solid transparent}
.f-brand{left:930px;top:3180px;width:180px;text-align:center}
.f-brand .brand-mark{width:64px;height:64px}
.f-brand .brand-name{font-size:16px}
.socials{display:flex;gap:8px;justify-content:center;margin-top:22px}
.socials span{width:26px;height:26px;border-radius:50%;border:2px solid #3b6fb6;background:var(--white)}
.socials span:last-child{border-color:var(--red)}
.bottom{left:0;top:3430px;width:1200px;height:52px;background:var(--white);display:flex;align-items:center;justify-content:center;font-size:12px;color:var(--ink)}
</style>
</head>
<body>

<header>
  <div class="abs brand">
    <div class="brand-mark"></div>
    <div class="brand-name">BRINDLE HARBOR<br>STUDIOS</div>
  </div>
  <div class="abs address">24 Larchmere Lane, Eastwick,<br>Northshire, UK, NW4 7QB</div>
  <div class="abs pin"><svg width="14" height="18" viewBox="0 0 14 18"><path d="M7 0C3 0 0 3 0 7c0 5 7 11 7 11s7-6 7-11c0-4-3-7-7-7z" fill="#e0323f"/><circle cx="7" cy="7" r="2.5" fill="#fff"/></svg></div>
  <div class="abs account">Welcome | Register | Sign In</div>
  <div class="abs search"><span>Search</span><svg width="12" height="12" viewBox="0 0 12 12"><circle cx="5" cy="5" r="3.8" fill="none" stroke="#333" stroke-width="1.6"/><path d="M8 8l3 3" stroke="#333" stroke-width="1.6"/></svg></div>
  <nav class="abs nav">
    <a>HOME</a><a>ABOUT ART STUDIO</a><a>PRODUCT</a><a>CATEGORY</a><a>BLOG</a><a>CONTACT US</a>
    <div class="cart"><svg width="24" height="20" viewBox="0 0 24 20"><path d="M0 2h4l3 11h12l3-8H6" fill="none" stroke="#fff" stroke-width="2"/><circle cx="9" cy="17" r="2" fill="#fff"/><circle cx="17" cy="17" r="2" fill="#fff"/></svg>$0.00</div>
  </nav>
</header>

<section class="abs hero" role="img" aria-label="Painting of two horses in expressive lavender and blue brushstrokes">
  <div class="abs arrow" style="left:40px;top:230px"><svg width="10" height="14"><path d="M8 1L2 7l6 6" stroke="#fff" stroke-width="2" fill="none"/></svg></div>
  <div class="abs arrow" style="right:40px;top:230px"><svg width="10" height="14"><path d="M2 1l6 6-6 6" stroke="#fff" stroke-width="2" fill="none"/></svg></div>
</section>
<div class="abs hero-badge"><span class="l1">NEW</span><span class="l2">ARTWORK</span><span class="l3"><span class="num">30</span><span class="pct"><small>off</small><b>%</b></span></span></div>

<h1 class="abs welcome-title">WELCOME TO <span>BRINDLE HARBOR STUDIOS</span></h1>
<p class="abs welcome-text">Lorem ipsum dolor sit amet, consectetur adipiscing elit, sed do eiusmod tempor incididunt ut labore et dolore magna aliqua. Ut enim ad minim veniam, quis nostrud exercitation ullamco laboris nisi ut aliquip ex ea commodo consequat. Duis aute irure dolor in reprehenderit in voluptate velit esse cillum dolore eu fugiat nulla pariatur. Excepteur sint occaecat cupidatat non proident, sunt in culpa qui officia deserunt mollit anim id est laborum</p>

<div class="abs frame big-frame" style="left:97px;top:905px"><div class="mat"><div class="art" role="img" aria-label="Black and white city street painting with a yellow taxi" style="background:linear-gradient(160deg,#d9d9d9,#777 60%,#c9b23a)"></div></div><div class="label">SED UT PERSPICIATIS UNDE OMNIS</div></div>
<div class="abs frame big-frame" style="left:441px;top:905px"><div class="mat"><div class="art" role="img" aria-label="Painting of a bicycle with a flower basket" style="background:linear-gradient(160deg,#d8cfc0,#9b7ba8 50%,#6f8b4a)"></div></div><div class="label">SED UT PERSPICIATIS UNDE OMNIS</div></div>
<div class="abs frame big-frame" style="left:785px;top:905px"><div class="mat"><div class="art" role="img" aria-label="Colourful abstract portrait painting" style="background:linear-gradient(160deg,#e8b33c,#c94a3a 50%,#3a6e9a)"></div></div><div class="label">SED UT PERSPICIATIS UNDE OMNIS</div></div>

<section class="abs banner" role="img" aria-label="Painting of a red tree and a city street with a clock tower and red bus"></section>
<div class="abs sale"><span class="s1">ON SALE</span><span class="s2">$60.00</span></div>
<h2 class="abs banner-title">BRINDLE HARBOR<br>STUDIOS</h2>
<p class="abs banner-text">Lorem ipsum dolor sit amet, consectetur adipiscing elit, sed do eiusmod tempor incididunt ut labore et dolore magna aliqua. Ut enim ad minim veniam, quis nostrud exercitation</p>
<div class="abs btn-shop">SHOP NOW!</div>

<div class="abs tabs"><div class="tab active">OUR PRODUCTS</div><div class="tab t2">FEATURED PRODUCTS</div><div class="tab t3">TOP IN SALES</div></div>

<div class="abs frame product-frame" style="left:97px;top:1864px"><div class="mat"><div class="art" role="img" aria-label="Purple tree with a deer painting" style="background:linear-gradient(160deg,#8a3fb5,#c14fc9 50%,#2fb39a)"></div></div></div>
<div class="abs frame product-frame" style="left:357px;top:1864px"><div class="mat"><div class="art" role="img" aria-label="Red autumn tree at sunset painting" style="background:linear-gradient(160deg,#3b5fa8,#e0623a 55%,#f2b23e)"></div></div></div>
<div class="abs frame product-frame" style="left:617px;top:1864px"><div class="mat"><div class="art" role="img" aria-label="Rainy Paris street painting" style="background:linear-gradient(160deg,#d9cfb8,#8e8a7c 55%,#c4743a)"></div></div></div>
<div class="abs frame product-frame" style="left:875px;top:1864px"><div class="mat"><div class="art" role="img" aria-label="Colourful cathedral city painting" style="background:linear-gradient(160deg,#e7d7c1,#d86a3c 55%,#3c6fa8)"></div></div></div>

<div class="abs" style="left:97px;top:2110px"><div class="p-name">Sed ut perspiciatis unde</div><div class="p-price">$200.00<span class="stars">★★★<span class="off">★★</span></span></div></div>
<div class="abs" style="left:357px;top:2110px"><div class="p-name">Sed ut perspiciatis unde</div><div class="p-price">$200.00<span class="stars">★★★<span class="off">★★</span></span></div></div>
<div class="abs" style="left:617px;top:2110px"><div class="p-name">Sed ut perspiciatis unde</div><div class="p-price">$200.00<span class="stars">★★★<span class="off">★★</span></span></div></div>
<div class="abs" style="left:875px;top:2110px"><div class="p-name">Sed ut perspiciatis unde</div><div class="p-price">$200.00<span class="stars">★★★<span class="off">★★</span></span></div></div>

<section class="abs features" role="img" aria-label="Dark background of thick painted brushstrokes">
  <div class="abs feature" style="left:66px;top:82px">
    <div class="f-icon" style="background:var(--orange)"><svg width="40" height="30" viewBox="0 0 40 30"><rect x="1" y="4" width="24" height="18" fill="#fff"/><path d="M25 10h8l6 6v6H25z" fill="#fff"/><circle cx="9" cy="25" r="4" fill="#fff" stroke="#f39a1e" stroke-width="2"/><circle cx="31" cy="25" r="4" fill="#fff" stroke="#f39a1e" stroke-width="2"/></svg></div>
    <div class="f-title">FREE SHIPPING ITEM</div>
    <div class="f-text">Lorem ipsum dolor sit amet, consectetur adipiscing<br>elit, sed do eiusmod tempor incididunt</div>
  </div>
  <div class="abs feature" style="left:419px;top:82px">
    <div class="f-icon" style="background:var(--blue)"><svg width="36" height="36" viewBox="0 0 36 36"><path d="M4 4h14l16 16-14 14L4 18z" fill="#fff"/><circle cx="11" cy="11" r="3" fill="#2aa3dc"/></svg></div>
    <div class="f-title">30 DAYS FREE RETURN</div>
    <div class="f-text">Lorem ipsum dolor sit amet, consectetur adipiscing<br>elit, sed do eiusmod tempor incididunt</div>
  </div>
  <div class="abs feature" style="left:772px;top:82px">
    <div class="f-icon" style="background:var(--green)"><svg width="32" height="38" viewBox="0 0 32 38"><path d="M2 2h28v18c0 8-14 16-14 16S2 28 2 20z" fill="#fff"/><path d="M10 10v10c0 4 6 7 6 7" stroke="#8cc63f" stroke-width="4" fill="none"/></svg></div>
    <div class="f-title">OUR GUARANTEE</div>
    <div class="f-text">Lorem ipsum dolor sit amet, consectetur adipiscing<br>elit, sed do eiusmod tempor incididunt</div>
  </div>
</section>

<h2 class="abs blogs-title">OUR BLOGS</h2>
<article class="abs blog" style="left:97px;top:2716px"><div class="img" role="img" aria-label="Fantasy landscape with a large moon" style="background:linear-gradient(180deg,#b6a98f,#6f7c8c 60%,#3c4550)"></div><div class="body"><div class="b-title">Nemo enim ipsam voluptatem</div><div class="b-meta"><svg width="12" height="12"><circle cx="6" cy="6" r="5" fill="none" stroke="#333" stroke-width="1.5"/><path d="M6 3v3h2" stroke="#333" stroke-width="1.3" fill="none"/></svg>3 minutes ago, 0 comments</div><div class="b-text">Lorem ipsum dolor sit amet, consectetur adipiscing elit, sed do eiusmod tempor incididunt</div></div></article>
<article class="abs blog" style="left:441px;top:2716px"><div class="img" role="img" aria-label="Fantasy temple scene under a blue sky" style="background:linear-gradient(180deg,#3e7fb8,#2b4d74 55%,#1c2a3c)"></div><div class="body"><div class="b-title">Nemo enim ipsam voluptatem</div><div class="b-meta"><svg width="12" height="12"><circle cx="6" cy="6" r="5" fill="none" stroke="#333" stroke-width="1.5"/><path d="M6 3v3h2" stroke="#333" stroke-width="1.3" fill="none"/></svg>3 minutes ago, 0 comments</div><div class="b-text">Lorem ipsum dolor sit amet, consectetur adipiscing elit, sed do eiusmod tempor incididunt</div></div></article>
<article class="abs blog" style="left:785px;top:2716px"><div class="img" role="img" aria-label="Colourful painting of dancers" style="background:linear-gradient(135deg,#e8a63a,#c9482f 50%,#7a2a5e)"></div><div class="body"><div class="b-title">Nemo enim ipsam voluptatem</div><div class="b-meta"><svg width="12" height="12"><circle cx="6" cy="6" r="5" fill="none" stroke="#333" stroke-width="1.5"/><path d="M6 3v3h2" stroke="#333" stroke-width="1.3" fill="none"/></svg>3 minutes ago, 0 comments</div><div class="b-text">Lorem ipsum dolor sit amet, consectetur adipiscing elit, sed do eiusmod tempor incididunt</div></div></article>

<footer>
  <div class="abs footer"></div>
  <div class="abs f-head" style="left:97px;top:3174px">SIGN UP FOR NEWSLETTER</div>
  <p class="abs news-text">Excepteur sint occaecat cupidatat non proident, sunt in culpa qui officia deserunt</p>
  <div class="abs news-input">Enter email</div>
  <div class="abs news-btn">SUBSCRIPTION</div>

  <div class="abs f-head" style="left:411px;top:3174px">CONTACT US</div>
  <div class="abs" style="left:411px;top:3218px;width:260px">
    <div class="contact-row"><svg width="12" height="16" viewBox="0 0 14 18"><path d="M7 0C3 0 0 3 0 7c0 5 7 11 7 11s7-6 7-11c0-4-3-7-7-7z" fill="#333"/><circle cx="7" cy="7" r="2.5" fill="#fff"/></svg><span>24 Larchmere Lane, Eastwick,<br>Northshire, UK, NW4 7QB</span></div>
    <div class="contact-row"><svg width="14" height="14" viewBox="0 0 14 14"><path d="M3 0l3 3-2 2c1 2 3 4 5 5l2-2 3 3-2 3C6 14 0 8 0 3z" fill="#333"/></svg><span>Phone: (480) 555-0142</span></div>
    <div class="contact-row"><svg width="14" height="12" viewBox="0 0 14 12"><rect x="0" y="1" width="14" height="10" fill="#333"/><path d="M0 1l7 5 7-5" stroke="#fff" fill="none"/></svg><span>info@brindleharborstudios.com</span></div>
  </div>

  <div class="abs f-head" style="left:736px;top:3174px">QUICK LINKS</div>
  <ul class="abs links" style="left:736px;top:3210px">
    <li>Shipping &amp; Returns</li><li>Secure Shopping</li><li>International Shipping</li><li>About Our Shop</li><li>Secure Shopping</li><li>Privacy Police</li>
  </ul>

  <div class="abs f-brand">
    <div class="brand-mark"></div>
    <div class="brand-name">BRINDLE HARBOR<br>STUDIOS</div>
    <div class="socials"><span></span><span></span><span></span><span></span></div>
  </div>
  <div class="abs bottom">©2017 Brindle Harbor Studios, All Rights Reserved.</div>
</footer>

</body>
</html>
```